Sales Flyer for Outdoor Kitchens

Looks to have a trifold flyer designed based off website content / projects. Use www.backyardhearthworks.com for content

```html
<!DOCTYPE html>
<html lang="en">
<head>
<meta charset="utf-8">
<title>Backyard Hearthworks – Trifold Flyer</title>
<link href="https://fonts.googleapis.com/css2?family=Abril+Fatface&family=Poppins:wght@400;600&display=swap" rel="stylesheet">
<style>
  :root{
    --green:#2f9e3c;
    --band:#3f6f12;
    --band-dark:#1d2a0b;
    --circle:#3d7a10;
    --paper:#e6e6e3;
    --paper-light:#f7f7f5;
    --ink:#1f1f1f;
    --gold:#e0b21c;
    --copper:#b8744c;
  }
  *{margin:0;padding:0;box-sizing:border-box}
  html,body{width:1200px;height:851px;overflow:hidden;background:#fff}
  .flyer{position:relative;width:1200px;height:851px;overflow:hidden}

  .panel{position:absolute;top:0;height:851px;overflow:hidden}
  .panel--services{left:0;width:391px;
    background:
      radial-gradient(circle at 30% 55%,rgba(255,255,255,.8),transparent 40%),
      radial-gradient(circle at 80% 20%,rgba(255,255,255,.7),transparent 35%),
      radial-gradient(ellipse at 50% 40%,var(--paper-light),var(--paper))}
  .panel--gallery{left:391px;width:405px;
    background:
      radial-gradient(ellipse 110px 80px at 200px 50px,rgba(214,178,120,.55),transparent 70%),
      linear-gradient(180deg,transparent 185px,#4a2e1c 185px,#5a3822 205px,transparent 225px),
      linear-gradient(180deg,#4a3222 0%,#3b2a1e 22%,#2d3126 48%,#2c3328 70%,#1e211c 100%)}
  .panel--reviews{left:796px;width:404px;
    background:
      radial-gradient(circle at 70% 60%,rgba(255,255,255,.8),transparent 40%),
      radial-gradient(ellipse at 50% 40%,var(--paper-light),var(--paper))}

  .ring{position:absolute;border-radius:50%;background:#fff;z-index:5}
  .ring span{position:absolute;border-radius:50%;background:var(--circle)}

  .lamp{position:absolute;top:0;width:84px;height:96px}
  .lamp .cord{position:absolute;left:41px;top:0;width:2px;height:46px;background:#555}
  .lamp .cap{position:absolute;left:34px;top:42px;width:16px;height:8px;border-radius:6px 6px 0 0;background:#9a5a38}
  .lamp .shade{position:absolute;left:2px;top:48px;width:80px;height:36px;border-radius:40px 40px 6px 6px;background:linear-gradient(180deg,#d9a07a,var(--copper) 45%,#7a4428)}
  .lamp .bulb{position:absolute;left:28px;top:80px;width:28px;height:8px;border-radius:0 0 14px 14px;background:#fff4cf;box-shadow:0 3px 10px rgba(255,220,140,.9)}

  .heading{position:absolute;display:flex;align-items:center;gap:4px;font-family:"Abril Fatface",serif;color:var(--green);letter-spacing:-0.5px;line-height:1;white-space:nowrap}
  .heading::before,.heading::after{content:"";display:block;height:3px;background:var(--green);flex:1}

  .band{position:absolute;top:156px;height:71px;
    background:
      radial-gradient(circle at 92% 30%,rgba(255,200,90,.45),transparent 18%),
      linear-gradient(90deg,var(--band),#4d7f15 60%,var(--band));
    border-top:4px solid var(--band-dark);border-bottom:4px solid var(--band-dark);color:#fff;font-family:"Abril Fatface",serif;white-space:nowrap}

  .photo{position:absolute;border:3px solid #1a1a1a;box-shadow:2px 3px 5px rgba(0,0,0,.35)}
  .label{position:absolute;font-family:"Abril Fatface",serif;font-size:11px;letter-spacing:.4px;color:var(--ink);text-align:center;text-transform:uppercase;white-space:nowrap}

  .gallery-title{position:absolute;left:5px;top:114px;width:395px;height:68px;background:#fff;border:3px solid #141414;display:flex;align-items:center;justify-content:center;gap:8px;font-family:"Abril Fatface",serif;font-size:40px;color:var(--green);z-index:2}
  .gallery-title::before,.gallery-title::after{content:"";width:36px;height:3px;background:var(--green)}

  .card{position:absolute;width:190px;height:176px;background:#fff;padding:5px;box-shadow:0 2px 6px rgba(0,0,0,.5);
    clip-path:polygon(0 0,100% 0,100% 92%,94% 95%,88% 91%,80% 96%,72% 92%,64% 97%,56% 92%,48% 96%,40% 91%,32% 96%,24% 92%,16% 97%,8% 92%,0 96%)}
  .card .shot{width:100%;height:155px}
  .tape{position:absolute;width:38px;height:9px;background:rgba(215,215,215,.9);z-index:3}

  .review{position:absolute;left:0;width:404px;text-align:center;font-family:"Poppins",sans-serif;color:var(--ink)}
  .review .name{font-weight:600;font-size:19px}
  .review .stars{color:var(--gold);font-size:15px;letter-spacing:6px;margin-top:1px}
  .review .quote{font-size:15.5px;line-height:25.6px;margin:8px auto 0}

  .scene{position:absolute;-webkit-mask-image:linear-gradient(180deg,transparent 0,#000 22%);mask-image:linear-gradient(180deg,transparent 0,#000 22%)}
</style>
</head>
<body>
<div class="flyer">

  <section class="panel panel--services">
    <div class="lamp" style="left:146px" role="img" aria-label="Copper pendant lamp"><div class="cord"></div><div class="cap"></div><div class="shade"></div><div class="bulb"></div></div>
    <h2 class="heading" style="left:5px;top:98px;width:376px;font-size:43px">WHAT WE DO</h2>
    <div class="band" style="left:0;width:391px;padding:7px 0 0 22px">
      <div style="font-size:27px;letter-spacing:.6px;line-height:1.05">OUR TURNKEY SERVICES</div>
      <div style="font-size:17.5px;margin-top:3px">We perform complete turnkey services</div>
    </div>

    <div class="photo" role="img" aria-label="Stainless outdoor kitchen grill with stone counter" style="left:11px;top:256px;width:174px;height:118px;background:
      radial-gradient(ellipse 60px 30px at 70px 35px,rgba(255,255,255,.8),transparent 70%),
      linear-gradient(90deg,transparent 70%,#3a3d42 70%,#5a5e64 100%),
      linear-gradient(180deg,#e2e2e0 0%,#b9bcc0 30%,#8d9196 60%,#d6d2ca 100%)"></div>
    <div class="label" style="left:11px;top:387px;width:174px">Outdoor Kitchens</div>

    <div class="photo" role="img" aria-label="White covered pavilion with dining set on patio" style="left:198px;top:257px;width:183px;height:116px;background:
      radial-gradient(ellipse 50px 35px at 90px 45px,#b98a5a,transparent 80%),
      linear-gradient(180deg,#9fc4e0 0%,#5f8a4a 22%,#f2f0ea 32%,#e8e4dc 55%,#6a625a 75%,#b8b2a8 100%)"></div>
    <div class="label" style="left:194px;top:387px;width:192px">Pavilions, Patios , Pergolas</div>

    <div class="photo" role="img" aria-label="Round stone fire pit glowing at dusk" style="left:97px;top:416px;width:176px;height:120px;background:
      radial-gradient(ellipse 20px 14px at 80px 62px,#ffcf6a,#e0702a 55%,transparent 100%),
      radial-gradient(ellipse 75px 25px at 85px 72px,#b9a08a,transparent 90%),
      linear-gradient(180deg,#2d4a3a 0%,#3e5a3a 25%,#7a5440 45%,#9a6a50 70%,#6a4a3a 100%)"></div>
    <div class="label" style="left:97px;top:548px;width:176px">Fire Pits</div>

    <div class="photo" role="img" aria-label="Backyard swimming pool with loungers" style="left:14px;top:572px;width:180px;height:120px;background:
      linear-gradient(180deg,#c6d4e2 0%,#eef1f3 22%,#7d8a96 38%,#f0f0ee 48%,#2bb6d6 58%,#5ed0e8 80%,#e2e2e0 92%)"></div>
    <div class="label" style="left:14px;top:704px;width:180px">Pools</div>

    <div class="photo" role="img" aria-label="Lit garden landscaping at night" style="left:213px;top:570px;width:166px;height:123px;background:
      radial-gradient(circle at 70% 25%,rgba(220,110,40,.8),transparent 30%),
      radial-gradient(circle at 40% 45%,rgba(150,200,60,.8),transparent 35%),
      radial-gradient(circle at 75% 70%,rgba(60,140,60,.8),transparent 35%),
      linear-gradient(135deg,#1e2a14,#3a5a1e 50%,#1c2616)"></div>
    <div class="label" style="left:205px;top:703px;width:182px">Landscaping , Lighting</div>

    <div class="scene" role="img" aria-label="Teak outdoor dining table with chairs" style="left:0;top:738px;width:330px;height:113px;background:
      radial-gradient(ellipse 180px 70px at 150px 120px,#b06a38,transparent 100%),
      linear-gradient(170deg,#8a4e26 0%,#a8652f 45%,#7a4320 100%)"></div>
  </section>

  <section class="panel panel--gallery" role="img" aria-label="Dimmed pavilion ceiling with antler chandelier">
    <h2 class="gallery-title">GALLERY</h2>

    <span class="tape" style="left:85px;top:225px"></span>
    <div class="card" style="left:8px;top:229px"><div class="shot" role="img" aria-label="Cedar pavilion on green lawn" style="background:
      radial-gradient(ellipse 70px 40px at 95px 70px,#a0603a,transparent 85%),
      linear-gradient(180deg,#4e7a3a 0%,#7aa66a 20%,#8a5a34 38%,#6a4a30 52%,#5a9a2a 62%,#3e7a22 100%)"></div></div>
    <span class="tape" style="left:284px;top:225px"></span>
    <div class="card" style="left:207px;top:229px"><div class="shot" role="img" aria-label="Pool house beside swimming pool" style="background:
      linear-gradient(180deg,#4e6a3e 0%,#7a9a6a 22%,#ecece6 38%,#8a8680 50%,#3cc6e0 62%,#6ad8ec 85%,#3ab0d0 100%)"></div></div>

    <span class="tape" style="left:85px;top:427px"></span>
    <div class="card" style="left:8px;top:431px"><div class="shot" role="img" aria-label="Covered patio lounge seating facing lawn" style="background:
      linear-gradient(180deg,#a0603a 0%,#8a4e2a 18%,#6a9a4a 35%,#5e8a3a 55%,#6a5a48 72%,#8a8278 100%)"></div></div>
    <span class="tape" style="left:284px;top:427px"></span>
    <div class="card" style="left:207px;top:431px"><div class="shot" role="img" aria-label="Built-in stainless grill close-up" style="background:
      radial-gradient(ellipse 70px 30px at 100px 30px,rgba(255,255,255,.8),transparent 75%),
      linear-gradient(180deg,#e6e6e4 0%,#a8acb0 35%,#7a7e84 65%,#d0ccc4 100%)"></div></div>

    <span class="tape" style="left:85px;top:626px"></span>
    <div class="card" style="left:8px;top:630px"><div class="shot" role="img" aria-label="Pavilion dining area with mounted TV" style="background:
      linear-gradient(180deg,#b0703a 0%,#8a5030 22%,#5e7a4a 38%,#6a4a3a 55%,#3a3a3a 80%,#5a5a5a 100%)"></div></div>
    <span class="tape" style="left:284px;top:626px"></span>
    <div class="card" style="left:207px;top:630px"><div class="shot" role="img" aria-label="Round stone fire pit at evening" style="background:
      radial-gradient(ellipse 18px 14px at 95px 85px,#ffcf6a,#e0702a 55%,transparent 100%),
      radial-gradient(ellipse 80px 30px at 95px 100px,#a89078,transparent 90%),
      linear-gradient(180deg,#2d4a3a 0%,#3e5a3a 25%,#7a5440 45%,#9a6a50 70%,#7a6a60 100%)"></div></div>
  </section>

  <section class="panel panel--reviews">
    <div class="lamp" style="left:165px" role="img" aria-label="Copper pendant lamp"><div class="cord"></div><div class="cap"></div><div class="shade"></div><div class="bulb"></div></div>
    <h2 class="heading" style="left:14px;top:98px;width:384px;font-size:43px">TESTIMONIALS</h2>
    <div class="band" style="left:0;width:404px;display:flex;align-items:center;justify-content:center;font-size:27px;letter-spacing:.6px">WHAT OUR CLIENTS SAY</div>

    <div class="review" style="top:272px">
      <div class="name">Carla M.</div>
      <div class="stars">★★★★★</div>
      <p class="quote" style="width:350px">“Mason is exceptional to work; his attention to detail, time management, and quality are outstanding. I highly recommend him.”</p>
    </div>
    <div class="review" style="top:451px">
      <div class="name">Priya S.</div>
      <div class="stars">★★★★★</div>
      <p class="quote" style="width:378px">“We recently had the pleasure of working with Backyard Hearthworks, LLC to design and construct our dream outdoor kitchen with a grill, burners, outdoor refrigerator and sink and we couldn’t be happier with the results. From the initial consultation to the final installation, every step of the process exceeded our expectations.”</p>
    </div>

    <div class="scene" role="img" aria-label="Wicker lounge chairs around fire table" style="left:0;top:716px;width:292px;height:135px;background:
      radial-gradient(ellipse 30px 18px at 145px 40px,rgba(255,200,120,.8),transparent 100%),
      radial-gradient(ellipse 60px 60px at 50px 90px,#7a6248,transparent 100%),
      radial-gradient(ellipse 60px 60px at 240px 90px,#7a6248,transparent 100%),
      linear-gradient(180deg,#8fb86a 0%,#6a8a4a 18%,#6a5440 40%,#4a3a2c 100%)"></div>
  </section>

  <div class="ring" style="left:-80px;top:-110px;width:187px;height:210px"><span style="left:-10px;top:-10px;width:185px;height:189px;background:radial-gradient(circle at 20% 25%,#f6c24a,#8a9a18 40%,var(--circle) 70%)"></span></div>
  <div class="ring" style="left:676px;top:-130px;width:241px;height:240px"><span style="left:17px;top:8px;width:207px;height:212px;background:linear-gradient(180deg,var(--circle),#4e8a12)"></span></div>
  <div class="ring" style="left:347px;top:436px;width:90px;height:90px"><span style="left:8px;top:8px;width:74px;height:74px"></span></div>
  <div class="ring" style="left:253px;top:749px;width:240px;height:240px"><span style="left:19px;top:19px;width:204px;height:210px"></span></div>
  <div class="ring" style="left:1069px;top:728px;width:290px;height:290px"><span style="left:24px;top:20px;width:260px;height:262px"></span></div>

</div>
</body>
</html>
```